Wine Lable

We Are Marrowby Estate Wines and we are designing a new bottle for our top end wine named "The Velvet Briar" I no exactly how i want the label to look and im searching for a talented designer to out my vision to life.

There will be 3 parts to this design.

Top Cover design with gold text wrapped around saying"The Velvet Briar" (See Fig 2)

The front label which i want same as attached (See fig 2)

The Rear label
(See Fig 2 for design)
(See Fig 3 for content)

and final bottle design how it will look together
Updates

Come on guys keep the designs coming

Project Deadline Extended
Reason: I have extended my deadline due to the break from work over the Christmas new year period. Extra consideration will be made

Target Market(s)

The High End wine consumers the bottle cost will be $100USD

Font styles to use
Decorative
Script

Requirements
Must have

• Top Cover design with gold text wrapped around saying"The Velvet Briar" (See Fig 2)
Black Rear Label with information and company name (Layout Fig 2) (Content Fig 3)
Gold and Black theme
The Text "Wine of Australia" somewhere on the bottle

```html
<!DOCTYPE html>
<html lang="en">
<head>
<meta charset="utf-8">
<title>The Velvet Briar – Wine Label</title>
<link rel="stylesheet" href="https://fonts.googleapis.com/css2?family=Great+Vibes&family=Cinzel:wght@600&family=Lora&display=swap">
<style>
  :root {
    --page: #ffffff;
    --label-black: #050505;
    --label-edge: #1c1c1c;
    --gold: #e7c04a;
    --gold-light: #f7e79a;
    --gold-deep: #b8901a;
    --band-gold: #d4b52c;
    --ink-dark: #1a1a1a;
  }
  html, body {
    margin: 0;
    width: 1200px;
    height: 1115px;
    overflow: hidden;
    background: var(--page);
  }
  .canvas {
    position: relative;
    width: 1200px;
    height: 1115px;
  }
  .front-label {
    position: absolute;
    left: 110px;
    top: 170px;
    width: 560px;
    height: 760px;
  }
  .capsule-band {
    position: absolute;
    left: 760px;
    top: 490px;
    width: 360px;
    height: 130px;
  }
  .label-body { fill: var(--label-black); stroke: var(--label-edge); stroke-width: 8; }
  .label-frame { fill: none; stroke: var(--gold); stroke-width: 3; }
  .emblem-ring { fill: none; stroke: var(--gold); stroke-width: 16; }
  .wine-name {
    font-family: "Great Vibes", cursive;
    font-size: 78px;
    fill: var(--gold);
  }
  .gold-rule { fill: var(--gold); }
  .estate-band { fill: var(--band-gold); }
  .estate-name {
    font-family: "Cinzel", serif;
    font-weight: 600;
    font-size: 25px;
    fill: var(--ink-dark);
    letter-spacing: 0.5px;
  }
  .origin {
    font-family: "Lora", serif;
    font-size: 19px;
    fill: var(--ink-dark);
  }
  .capsule-body { fill: #141414; }
  .capsule-name {
    font-family: "Great Vibes", cursive;
    font-size: 44px;
    fill: var(--gold);
  }
  .capsule-line { stroke: var(--gold); stroke-width: 2.5; }
</style>
</head>
<body>
<main class="canvas">
  <svg class="front-label" viewBox="0 0 560 760" xmlns="http://www.w3.org/2000/svg">
    <defs>
      <radialGradient id="emblemFill" cx="45%" cy="40%" r="65%">
        <stop offset="0%" stop-color="var(--gold-light)"/>
        <stop offset="100%" stop-color="var(--gold-deep)"/>
      </radialGradient>
    </defs>
    <path class="label-body" d="M4,226 H76 V196 C76,86 166,4 280,4 C394,4 484,86 484,196 V226 H556 V736 Q556,756 536,756 H24 Q4,756 4,736 Z"/>
    <path class="label-frame" d="M22,240 H92 V198 C92,100 176,22 280,22 C384,22 468,100 468,198 V240 H538 V708 H22 Z"/>
    <circle class="emblem-ring" cx="280" cy="215" r="150"/>
    <circle cx="280" cy="215" r="118" fill="url(#emblemFill)" opacity="0.85" role="img" aria-label="Gold grape cluster and vine leaf emblem"/>
    <text class="wine-name" x="280" y="500" text-anchor="middle">The Velvet Briar</text>
    <rect class="gold-rule" x="22" y="588" width="516" height="8"/>
    <rect class="estate-band" x="22" y="610" width="516" height="90"/>
    <text class="estate-name" x="280" y="650" text-anchor="middle">MARROWBY ESTATE WINES</text>
    <text class="origin" x="280" y="680" text-anchor="middle">Wine of Australia</text>
  </svg>

  <svg class="capsule-band" viewBox="0 0 360 130" xmlns="http://www.w3.org/2000/svg">
    <rect class="capsule-body" x="0" y="0" width="360" height="130" rx="6"/>
    <text class="capsule-name" x="180" y="68" text-anchor="middle">The Velvet Briar</text>
    <line class="capsule-line" x1="0" y1="88" x2="360" y2="88"/>
    <line class="capsule-line" x1="0" y1="98" x2="360" y2="98"/>
  </svg>
</main>
</body>
</html>
```